Lo Mara Menu Design Project

This project is pretty straight forward. You will be given 3 files which include the following:
1. Our proposed menu
2. Our Company logo
3. A sample menu on what we are looking for design wise

Your job is to create a visually pleasing menu that is simple, clean and fresh. Please refer to our home website for additional information. (www.lomara-eats.com) Must be in eps or equivalent format.

Target Market(s)

20s to 40s

Industry/Entity Type

It Company

Requirements
Must have
• Company log
Must be in EPS format

```html
<!DOCTYPE html>
<html lang="en">
<head>
<meta charset="utf-8">
<title>Lo Mara Menu</title>
<link rel="stylesheet" href="https://fonts.googleapis.com/css2?family=Arimo:wght@400;700&family=Tinos:wght@700&display=swap">
<style>
  :root {
    --backdrop: #5b341c;
    --board-dark: #141414;
    --board-mid: #2b2b2b;
    --text: #ffffff;
    --accent: #e0231b;
  }
  html, body {
    margin: 0;
    padding: 0;
    width: 1045px;
    height: 1200px;
    overflow: hidden;
    background: var(--backdrop);
  }
  .canvas {
    position: relative;
    width: 1045px;
    height: 1200px;
  }
  .menu-board {
    position: absolute;
    left: 125px;
    top: 81px;
    width: 861px;
    height: 1064px;
    background:
      radial-gradient(ellipse at 50% 40%, var(--board-mid) 0%, var(--board-dark) 75%);
    box-shadow: 0 0 18px rgba(0,0,0,0.55);
  }
  .menu-section {
    position: absolute;
    width: 420px;
    text-align: center;
    color: var(--text);
  }
  .section-title {
    display: inline-block;
    margin: 0;
    padding: 0 2px 5px;
    font-family: "Arimo", "Helvetica Neue", Arial, sans-serif;
    font-weight: 400;
    font-size: 50px;
    line-height: 52px;
    border-bottom: 3px solid var(--accent);
  }
  .dish-list {
    list-style: none;
    margin: 22px 0 0;
    padding: 0;
    font-family: "Tinos", "Times New Roman", serif;
    font-weight: 700;
    font-size: 18px;
    line-height: 27px;
  }
  .section-chicken { left: 99px; top: 170px; }
  .section-beef { left: 546px; top: 170px; }
  .section-noodles { left: 326px; top: 472px; }
  .section-seafood { left: 108px; top: 792px; }
  .section-vegetables { left: 531px; top: 792px; }
  .brand-name {
    position: absolute;
    left: 820px;
    top: 1068px;
    margin: 0;
    font-family: "Arimo", "Helvetica Neue", Arial, sans-serif;
    font-weight: 700;
    font-size: 30px;
    line-height: 1;
    color: var(--accent);
  }
</style>
</head>
<body>
<div class="canvas">
  <main class="menu-board">
    <section class="menu-section section-chicken" style="left:-26px;top:89px;">
      <h2 class="section-title">Chicken</h2>
      <ul class="dish-list">
        <li>General Tso?s Chicken</li>
        <li>Kung Pao Chicken</li>
        <li>Orange Chicken</li>
        <li>Chicken Lettuce Cups</li>
        <li>Moo Goo Gai Pan</li>
      </ul>
    </section>
    <section class="menu-section section-beef" style="left:421px;top:89px;">
      <h2 class="section-title">Beef/Pork</h2>
      <ul class="dish-list">
        <li>Mongolian Beef</li>
        <li>Beef &amp; Broccoli</li>
        <li>Pepper Steak</li>
        <li>Sweet &amp; Sour Pork</li>
        <li>Sliced BBQ Pork</li>
      </ul>
    </section>
    <section class="menu-section section-noodles" style="left:201px;top:391px;">
      <h2 class="section-title">Noodles</h2>
      <ul class="dish-list">
        <li>Chow Mein</li>
        <li>Lo Mein</li>
        <li>Pad Thai</li>
        <li>Singapore Noodles</li>
        <li>Seafood Noodles</li>
      </ul>
    </section>
    <section class="menu-section section-seafood" style="left:-17px;top:711px;">
      <h2 class="section-title">Seafood</h2>
      <ul class="dish-list">
        <li>Shrimp w/ Snow Peas</li>
        <li>Scallops w/ black bean sauce</li>
        <li>Fish w/ ginger soy</li>
        <li>Kung Pao 3 treasures</li>
        <li>Walnut Shrimp</li>
      </ul>
    </section>
    <section class="menu-section section-vegetables" style="left:406px;top:711px;">
      <h2 class="section-title">Vegetables</h2>
      <ul class="dish-list">
        <li>Spinach w/ garli</li>
        <li>Bak Choy w/ Mushooms</li>
        <li>Fragrant Vegetables</li>
        <li>Schezuan String Beans</li>
        <li>Spicy Garlic Eggplant</li>
      </ul>
    </section>
    <p class="brand-name" style="left:695px;top:987px;">Lo Mara</p>
  </main>
</div>
</body>
</html>
```